Dusty Spur Outfitters Home Page

I need a logo and page design for my home page, maybe some background color suggestions to go with it. I want the logo to project "vintage" and "western wear" but not be your typical trite western saddle and gun type thing.
http://www.dustyspuroutfitters.example/store/cart.php
Not looking for page coding just logo and other design elements to lay in over the site's template to make it "pop"
Reason: Have to finalize the design.
Target Market(s)
My customers are 70/30 men to women.
Industry/Entity Type
Gun

```html
<!DOCTYPE html>
<html lang="en">
<head>
<meta charset="utf-8">
<title>Dusty Spur Outfitters – Header Colour Options</title>
<link rel="stylesheet" href="https://fonts.googleapis.com/css2?family=Lato:wght@700;900&family=Pacifico&display=swap">
<style>
  :root {
    --canvas-beige: #cdb99a;
    --trim-brown: #4d372a;
    --trim-edge: #3a291f;
    --band-charcoal: #272727;
    --band-espresso: #2a1b12;
    --band-slate: #3f534d;
    --cream: #e8dcc0;
    --tagline: #d8d1bd;
    --ink: #2e2a25;
    --star-red: #b8321f;
  }
  * { margin: 0; padding: 0; box-sizing: border-box; }
  html, body { width: 1200px; height: 1000px; overflow: hidden; }
  body {
    background: var(--canvas-beige);
    font-family: "Lato", Arial, sans-serif;
    position: relative;
  }
  .header-option {
    position: absolute;
    left: 0;
    width: 1200px;
    height: 166px;
    background: var(--trim-brown);
    border-top: 2px solid var(--trim-edge);
    box-shadow: 0 4px 5px rgba(60, 40, 25, 0.45);
  }
  .header-option--charcoal { top: 147px; }
  .header-option--espresso { top: 417px; }
  .header-option--slate { top: 687px; }
  .header-band {
    position: absolute;
    left: 0;
    top: 16px;
    width: 100%;
    height: 131px;
    border-bottom: 3px solid var(--trim-edge);
  }
  .header-option--charcoal .header-band { background: var(--band-charcoal); }
  .header-option--espresso .header-band { background: var(--band-espresso); }
  .header-option--slate .header-band { background: var(--band-slate); }
  .brand {
    position: absolute;
    left: 62px;
    top: 58px;
    display: flex;
    align-items: center;
    gap: 12px;
  }
  .brand-mark {
    width: 22px;
    height: 22px;
    border-radius: 50%;
    background: var(--star-red);
  }
  .brand-name {
    font-weight: 900;
    font-size: 31px;
    color: var(--cream);
    letter-spacing: 0.5px;
    line-height: 1;
  }
  .tagline {
    position: absolute;
    left: 476px;
    top: 84px;
    font-family: "Pacifico", cursive;
    font-size: 21px;
    color: var(--tagline);
    line-height: 1;
    white-space: nowrap;
  }
  .search {
    position: absolute;
    left: 901px;
    top: 52px;
    display: flex;
    align-items: center;
    gap: 11px;
  }
  .search-field {
    width: 173px;
    height: 30px;
    border-radius: 15px;
    background: var(--cream);
    color: var(--ink);
    font-weight: 700;
    font-size: 17px;
    line-height: 30px;
    padding-left: 17px;
  }
  .search-button {
    color: var(--cream);
    font-weight: 700;
    font-size: 18px;
  }
</style>
</head>
<body>
  <section class="header-option header-option--charcoal">
    <div class="header-band"></div>
    <div class="brand"><span class="brand-mark"></span><span class="brand-name">Dusty Spur Outfitters</span></div>
    <p class="tagline">Brand-New Retro Styled Western Wear</p>
    <div class="search"><span class="search-field">Search...</span><span class="search-button">GO!</span></div>
  </section>

  <section class="header-option header-option--espresso">
    <div class="header-band"></div>
    <div class="brand"><span class="brand-mark"></span><span class="brand-name">Dusty Spur Outfitters</span></div>
    <p class="tagline">Brand-New Retro Styled Western Wear</p>
    <div class="search"><span class="search-field">Search...</span><span class="search-button">GO!</span></div>
  </section>

  <section class="header-option header-option--slate">
    <div class="header-band"></div>
    <div class="brand"><span class="brand-mark"></span><span class="brand-name">Dusty Spur Outfitters</span></div>
    <p class="tagline">Brand-New Retro Styled Western Wear</p>
    <div class="search"><span class="search-field">Search...</span><span class="search-button">GO!</span></div>
  </section>
</body>
</html>
```